Business Intelligence Application - Reporting Menu and Report Criteria Design

Looking for a fresh, effective and user friendly view for the menu structure and reporting criteria screen format for a business reporting application. Initial format completed, content structure is in place, but we need the 'wow' design.. as its a serious professional report/BI tool it has to fall within certain guidelines for clarity and graphics..but we want it to be slick, friendly, great user experience. There is a large amount of complex content to fit into a small space and we need it to be very inviting, modern and intuitive.. If interested, please review the attachment. We have live screens in operation, but feel these could be improved and looking forward to seeing what great creative suggestions could be made. Please review work done to date in the attached.. We are not looking for a total re-design of everything, all the basic business content/structure is there.. but tell us what we could do to improve this in terms of graphic design... particularly the criteria screens.. thanks!
Updates

Reason: Need a few more days to review designs - thanks for all submissions so far, we will make a selection shortly.

Target Market(s)

Business analysts, hotel operations teams, finance analysts hospitality industry

Industry/Entity Type

Hospitality

Coding

Coded - Design and coding required

Number of Pages Required

4 page

Font styles to use
Sans Serif
Other font styles liked:
• Candara, please see example in deck

Colors
3276b5
3176b5
0255a3
85acd3
33a6d7
cee9f5
85cae6

Requirements
Must have
• sharp clear, logical menu structure, (currently it has 'clicks to sub-menus, we need hover over, slide to sub-menus..) colour, styling.. and most focus on revision of criteria.. right now is somewhat heavy, cumbersome.. keep colour and friendly intuitive process steps.. its heavy analytical stuff.. best of luck!
Should not have
• No grey fonts on white or grey screens! many business apps are not readable or sharp.. or fonts are too small.. colourless, so please avoid that.. see our deck - sharp dark (navy) or black fonts on white, or light shading..

```html
<!DOCTYPE html>
<html lang="en">
<head>
<meta charset="utf-8">
<title>RQ Insight – Property Search</title>
<link href="https://fonts.googleapis.com/css2?family=Open+Sans:ital,wght@0,400;0,600;1,400&display=swap" rel="stylesheet">
<style>
  :root{
    --header:#135494;
    --sidebar:#2f72b2;
    --sidebar-active:#0255a3;
    --sidebar-line:#4a87c0;
    --canvas:#cdd5da;
    --ink:#0f4f8f;
    --link:#3276b5;
    --submenu:#dcecf5;
    --submenu-hover:#eef5fa;
    --field:#dedede;
    --field-line:#b9c4cc;
    --row:#dcdcdc;
    --row-head:#cfdbe3;
    --text-dark:#4a4a4a;
    --white:#ffffff;
    --chip:#d7e5f1;
  }
  *{box-sizing:border-box;margin:0;padding:0}
  html,body{width:1200px;height:656px;overflow:hidden}
  body{font-family:"Open Sans",sans-serif;background:var(--canvas);position:relative}

  .topbar{position:absolute;left:0;top:0;width:1200px;height:80px;background:var(--header)}
  .brand{position:absolute;left:22px;top:14px;font-size:38px;font-weight:400;color:#e9eef4;letter-spacing:0.5px}
  .welcome{position:absolute;right:165px;top:21px;text-align:right;color:var(--white)}
  .welcome .hello{font-size:16px;line-height:20px}
  .welcome .date{font-size:9.5px;font-style:italic;line-height:14px}
  .avatar{position:absolute;left:1045px;top:24px;width:32px;height:32px;border-radius:50%;background:linear-gradient(135deg,#c9a487,#7c5a45)}
  .icon-btn{position:absolute;top:24px;width:32px;height:32px;border-radius:50%;background:var(--chip);display:flex;align-items:center;justify-content:center}
  .icon-btn.bell{left:1101px}
  .icon-btn.exit{left:1147px}

  .sidebar{position:absolute;left:0;top:80px;width:240px;height:576px;background:var(--sidebar)}
  .nav-item{position:absolute;left:0;width:240px;display:flex;align-items:center;color:var(--white);font-size:17px;border-bottom:1px solid var(--sidebar-line)}
  .nav-item.active{background:var(--sidebar-active)}
  .nav-item svg{position:absolute;left:24px}
  .nav-item span{position:absolute;left:58px}

  .page-title{position:absolute;left:264px;top:106px;font-size:34px;font-weight:600;color:var(--ink)}
  .field-label{position:absolute;font-size:15px;color:var(--ink)}
  .field{position:absolute;width:280px;height:43px;background:var(--field);border:1px solid var(--field-line);font-size:12.5px;color:var(--text-dark);padding:14px 16px}

  .property-table{position:absolute;left:264px;top:371px;width:911px;border:1px solid var(--field-line)}
  .property-table .head{height:44px;background:var(--row-head);font-size:15px;color:var(--ink);padding:12px 16px}
  .property-table .row{display:flex;background:var(--row);border-top:1px solid #c7cdd2;font-size:15px;color:var(--text-dark)}
  .property-table .row div{display:flex;align-items:center}
  .property-table .row .name{width:455px;padding-left:16px;border-right:1px solid #c7cdd2}
  .property-table .row .code{padding-left:88px}

  .footer{position:absolute;left:0;top:616px;width:1200px;text-align:center;font-size:12px;color:var(--ink)}

  .submenu{position:absolute;list-style:none}
  .submenu li{display:flex;align-items:center;font-size:13px;height:40px;border-bottom:1px solid #c9dce8}
  .submenu li::before{content:"›";margin-right:10px;font-size:14px}
  .submenu.level-one{left:240px;top:96px;width:140px;background:var(--submenu)}
  .submenu.level-one li{color:var(--ink);padding-left:18px}
  .submenu.level-one li.open{background:var(--submenu-hover)}
  .submenu.level-two{left:380px;top:185px;width:196px;background:var(--white)}
  .submenu.level-two li{color:var(--link);padding-left:18px;border-bottom-color:#e3e9ee}
</style>
</head>
<body>
  <header class="topbar">
    <div class="brand">RQ Insight</div>
    <div class="welcome">
      <div class="hello">Welcome Admin</div>
      <div class="date">Tuesday 5 October, 2017</div>
    </div>
    <div class="avatar" role="img" aria-label="User profile photo"></div>
    <div class="icon-btn bell">
      <svg width="14" height="14" viewBox="0 0 14 14"><path d="M7 1.5c-2.3 0-3.8 1.7-3.8 4v3L2 10.2h10L10.8 8.5v-3c0-2.3-1.5-4-3.8-4z" fill="#135494"/><circle cx="7" cy="11.8" r="1.3" fill="#135494"/></svg>
    </div>
    <div class="icon-btn exit">
      <svg width="14" height="14" viewBox="0 0 14 14"><path d="M8 2h3.5v10H8" fill="none" stroke="#135494" stroke-width="1.6"/><path d="M2 7h6M5.5 4.5L8 7 5.5 9.5" fill="none" stroke="#135494" stroke-width="1.8"/></svg>
    </div>
  </header>

  <nav class="sidebar">
    <div class="nav-item active" style="top:0;height:85px">
      <svg width="16" height="16" viewBox="0 0 16 16"><circle cx="8" cy="4.5" r="3.3" fill="#fff"/><path d="M2 15c0-4 2.5-6 6-6s6 2 6 6z" fill="#fff"/></svg>
      <span>Admin</span>
    </div>
    <div class="nav-item" style="top:85px;height:80px">
      <svg width="20" height="16" viewBox="0 0 20 16"><circle cx="10" cy="5" r="3" fill="#fff"/><circle cx="4" cy="6" r="2.2" fill="#fff"/><circle cx="16" cy="6" r="2.2" fill="#fff"/><path d="M4 15c0-3.5 2.5-5.5 6-5.5s6 2 6 5.5z" fill="#fff"/><path d="M0 13c0-2.5 1.6-4 4-4l1 .2L3.5 13z M20 13c0-2.5-1.6-4-4-4l-1 .2 1.5 3.8z" fill="#fff"/></svg>
      <span>Mangement</span>
    </div>
    <div class="nav-item" style="top:165px;height:81px">
      <svg width="18" height="12" viewBox="0 0 18 12"><path d="M1 6c2-3.5 4.8-5 8-5s6 1.5 8 5c-2 3.5-4.8 5-8 5S3 9.5 1 6z" fill="#fff"/><circle cx="9" cy="6" r="2.6" fill="#2f72b2"/></svg>
      <span>My View</span>
    </div>
    <div class="nav-item" style="top:246px;height:81px">
      <svg width="16" height="16" viewBox="0 0 16 16"><circle cx="6.5" cy="6.5" r="4.5" fill="none" stroke="#fff" stroke-width="2.2"/><path d="M10 10l4.5 4.5" stroke="#fff" stroke-width="2.6" stroke-linecap="round"/></svg>
      <span>Property Search</span>
    </div>
    <div class="nav-item" style="top:327px;height:79px">
      <svg width="18" height="16" viewBox="0 0 18 16"><circle cx="6" cy="9" r="4.3" fill="none" stroke="#fff" stroke-width="2.6" stroke-dasharray="2 1.4"/><circle cx="6" cy="9" r="1.6" fill="#fff"/><circle cx="13.5" cy="4.5" r="2.8" fill="none" stroke="#fff" stroke-width="2" stroke-dasharray="1.5 1.1"/><circle cx="14" cy="12.5" r="2.3" fill="none" stroke="#fff" stroke-width="1.8" stroke-dasharray="1.3 1"/></svg>
      <span>Intel</span>
    </div>
    <div class="nav-item" style="top:406px;height:80px">
      <svg width="12" height="16" viewBox="0 0 12 16"><path d="M6 1.5a4.3 4.3 0 0 0-2.5 7.8V11h5V9.3A4.3 4.3 0 0 0 6 1.5z" fill="none" stroke="#fff" stroke-width="1.6"/><path d="M3.8 13h4.4M4.5 15h3" stroke="#fff" stroke-width="1.5"/></svg>
      <span>Planning</span>
    </div>
  </nav>

  <main>
    <h1 class="page-title">Property Search</h1>

    <label class="field-label" style="left:579px;top:171px">Search ID</label>
    <div class="field" style="left:580px;top:195px"></div>
    <label class="field-label" style="left:894px;top:171px">Search Product</label>
    <div class="field" style="left:895px;top:195px"></div>

    <label class="field-label" style="left:263px;top:267px">Divisions</label>
    <div class="field" style="left:264px;top:291px">North America</div>
    <label class="field-label" style="left:579px;top:267px">Regions</label>
    <div class="field" style="left:580px;top:291px"></div>
    <label class="field-label" style="left:894px;top:267px">Areas</label>
    <div class="field" style="left:895px;top:291px"></div>

    <section class="property-table">
      <div class="head">Select Property</div>
      <div class="row" style="height:44px"><div class="name">Grand Central</div><div class="code">RHDOH</div></div>
      <div class="row" style="height:48px"><div class="name">Sandy Beach Hotel</div><div class="code">123</div></div>
      <div class="row" style="height:40px"><div class="name">Aliquam erat volutpat</div><div class="code">Pellentesque</div></div>
      <div class="row" style="height:40px"><div class="name">Quisque aliquet ex nec est</div><div class="code">Aenean</div></div>
    </section>

    <footer class="footer">Copyright &nbsp;©&nbsp; 2017 &nbsp;RQ Insight. &nbsp;All rights reserved.</footer>
  </main>

  <ul class="submenu level-one">
    <li>Registration</li>
    <li>User Access</li>
    <li class="open">Setup</li>
    <li>Data Imports</li>
  </ul>

  <ul class="submenu level-two">
    <li>Merket Segments</li>
    <li>Banquet &amp; Catering</li>
    <li>Outlets/F&amp;B Service</li>
    <li>Other Income</li>
    <li>IMpact Dates</li>
    <li>Inventory</li>
    <li>Geo/Location</li>
    <li>Distribution Channels</li>
  </ul>
</body>
</html>
```